Plumbing & Heating company

A leaflet containing -

Company name - Larkfield Plumbing Solutions
logo
Mobile number - 07700 914062
Landline - 01632 870215
Email - Info@larkfieldplumbing.example
website - Larkfield-plumbing.example
Social media logos - insta, Facebook

services we offer

- Boiler replacements (free quote)
- General plumbing & heating
- Tap replacements
- 1st & 2nd
- New builds & Extensions
- Cylinder replcemets

```html
<!DOCTYPE html>
<html lang="en">
<head>
<meta charset="utf-8">
<title>Larkfield Plumbing Solutions – Plumbing Services Leaflet</title>
<link rel="stylesheet" href="https://fonts.googleapis.com/css2?family=Anton&family=Montserrat:wght@400;500;700;800&family=Oswald:wght@400;500&display=swap">
<style>
  :root {
    --backdrop: #c6c6c6;
    --paper: #ffffff;
    --navy: #0b4a8f;
    --navy-deep: #0c4695;
    --sky: #0a88c9;
    --ink: #1c2a4a;
    --yellow: #f7c21e;
    --orange: #f26f30;
    --red: #ee4237;
    --rule: #c9ccd2;
    --white: #ffffff;
  }
  * { margin: 0; padding: 0; box-sizing: border-box; }
  html, body { width: 1200px; height: 1078px; overflow: hidden; }
  body { background: var(--backdrop); font-family: "Montserrat", sans-serif; position: relative; }

  .leaflet {
    position: absolute; left: 254px; top: 50px; width: 692px; height: 978px;
    background: var(--paper); overflow: hidden;
    box-shadow: 0 0 6px rgba(0,0,0,0.18);
  }
  .leaflet-art { position: absolute; inset: 0; }

  .brand { position: absolute; left: 42px; top: 24px; display: flex; align-items: center; gap: 8px; }
  .brand-dot { width: 26px; height: 26px; border-radius: 50%; background: var(--navy); }
  .brand-name { font-weight: 800; color: var(--navy); font-size: 13px; line-height: 1.15; text-transform: uppercase; letter-spacing: 0.4px; }

  .follow { position: absolute; left: 553px; top: 28px; color: var(--white); font-weight: 700; font-size: 11.5px; letter-spacing: 0.3px; }
  .social { position: absolute; left: 548px; top: 47px; display: flex; gap: 3px; }
  .social-dot { width: 19px; height: 19px; border-radius: 50%; background: var(--yellow); }

  .photo { position: absolute; border: 3px solid var(--white); box-shadow: 0 1px 4px rgba(0,0,0,0.25); }
  .photo-pipework { left: 41px; top: 390px; width: 329px; height: 402px; border-top-right-radius: 34px;
    background: linear-gradient(160deg, #a89b8e 0%, #8a8077 40%, #b98566 70%, #8c8078 100%); }
  .photo-cylinder { left: 402px; top: 324px; width: 198px; height: 261px; border-radius: 4px;
    background: linear-gradient(180deg, #f1efec 0%, #e4e1dc 60%, #c9b49b 85%, #9a958e 100%); }
  .photo-boiler { left: 18px; top: 740px; width: 150px; height: 144px; border-radius: 4px;
    background: linear-gradient(90deg, #a97b55 0%, #c79b70 45%, #ecebe8 60%, #b98b62 100%); }

  .services { position: absolute; left: 414px; top: 622px; color: var(--white); }
  .services-title { color: var(--yellow); font-weight: 700; font-size: 17.5px; letter-spacing: 0.2px; margin-bottom: 7px; }
  .services-list { list-style: none; }
  .services-list li { display: flex; align-items: center; gap: 8px; font-size: 12.2px; font-weight: 400; height: 22px; padding-left: 5px; letter-spacing: 0.2px; }
  .tick { width: 13px; height: 13px; flex: none; }

  .booking { position: absolute; left: 283px; top: 805px; color: var(--white); }
  .booking-title { color: var(--yellow); font-weight: 700; font-size: 20px; margin-bottom: 2px; }
  .contact { display: flex; align-items: center; gap: 7px; }
  .contact-icon { width: 18px; height: 18px; border-radius: 50%; background: var(--white); flex: none; display: flex; align-items: center; justify-content: center; }
  .contact-icon svg { width: 11px; height: 11px; }
  .contact-phone { font-size: 22px; font-weight: 800; height: 30px; letter-spacing: 0.4px; }
  .contact-line { font-size: 13px; font-weight: 500; height: 24px; text-transform: uppercase; letter-spacing: 1px; }
</style>
</head>
<body>
<main class="leaflet">
  <svg class="leaflet-art" viewBox="0 0 692 978" width="692" height="978">
    <defs>
      <linearGradient id="blue-field" x1="0" y1="0" x2="0" y2="1">
        <stop offset="0" stop-color="#0a8ccc"/>
        <stop offset="0.45" stop-color="#0d5aa8"/>
        <stop offset="1" stop-color="#0c4695"/>
      </linearGradient>
      <linearGradient id="headline-fill" gradientUnits="userSpaceOnUse" x1="0" y1="151" x2="0" y2="258">
        <stop offset="0.5" stop-color="#f26f30"/>
        <stop offset="0.5" stop-color="#ee4237"/>
      </linearGradient>
      <linearGradient id="tag-fill" x1="0" y1="0" x2="0" y2="1">
        <stop offset="0" stop-color="#0d64b0"/>
        <stop offset="1" stop-color="#0b4a8f"/>
      </linearGradient>
    </defs>

    <path class="logo-arc" d="M0,68 C40,95 140,100 210,85 C240,70 232,20 224,0" fill="none" stroke="#d7d9dd" stroke-width="1"/>

    <path class="blue-field" d="M502,2 L692,2 L692,978 L5,978 L560,320 C592,280 582,232 528,190 C452,132 440,58 502,2 Z" fill="url(#blue-field)"/>

    <path class="accent-curve" d="M370,2 C378,60 450,76 520,96 C592,118 585,200 556,272 C520,360 300,650 2,913" fill="none" stroke="var(--yellow)" stroke-width="1.6"/>
    <path class="dashed-arc" d="M598,229 C614,250 618,285 602,307" fill="none" stroke="#ffffff" stroke-width="1.2" stroke-dasharray="5 4"/>

    <path class="frame-line" d="M19,585 L19,382 Q19,366 35,366 L284,366" fill="none" stroke="#1c2a5a" stroke-width="1.6"/>
    <path class="frame-line" d="M605,300 L612,300 Q620,300 620,308 L620,401" fill="none" stroke="#ffffff" stroke-width="1.4"/>
    <path class="frame-line" d="M176,848 L176,888 Q176,896 168,896 L107,896" fill="none" stroke="#ffffff" stroke-width="1.4"/>
    <path class="frame-line" d="M401,546 L390,546 L390,658 L371,658" fill="none" stroke="var(--yellow)" stroke-width="1.6"/>

    <rect class="headline-tag" x="100" y="92" width="179" height="47" rx="4" fill="url(#tag-fill)"/>
    <text x="110" y="130" font-family="Oswald, sans-serif" font-weight="500" font-size="34" fill="#ffffff" textLength="159" lengthAdjust="spacingAndGlyphs">LOOKING</text>
    <text x="284" y="130" font-family="Oswald, sans-serif" font-weight="400" font-size="24" fill="var(--ink)" textLength="47" lengthAdjust="spacingAndGlyphs">FOR</text>

    <text class="headline" x="36" y="258" font-family="Anton, sans-serif" font-size="124" fill="url(#headline-fill)" textLength="422" lengthAdjust="spacingAndGlyphs">PLUMBING</text>

    <line x1="46" y1="306" x2="139" y2="306" stroke="var(--rule)" stroke-width="1.6"/>
    <line x1="350" y1="306" x2="443" y2="306" stroke="var(--rule)" stroke-width="1.6"/>
    <text class="subhead" x="151" y="331" font-family="Anton, sans-serif" font-size="60" fill="var(--navy)" textLength="191" lengthAdjust="spacingAndGlyphs">SERVICES</text>
  </svg>

  <div class="brand">
    <span class="brand-dot"></span>
    <span class="brand-name">Larkfield<br>Plumbing Solutions</span>
  </div>

  <p class="follow">FOLLOW US NOW</p>
  <div class="social" aria-label="Social media links">
    <span class="social-dot" aria-label="Social profile one"></span>
    <span class="social-dot" aria-label="Social profile two"></span>
  </div>

  <div class="photo photo-pipework" role="img" aria-label="Photo of copper pipework laid between timber floor joists"></div>
  <div class="photo photo-cylinder" role="img" aria-label="Photo of an installed hot water cylinder and wall-hung boiler with copper pipes"></div>
  <div class="photo photo-boiler" role="img" aria-label="Photo of a new boiler installation with pipework on a timber wall"></div>

  <section class="services">
    <h2 class="services-title">SERVICES WE OFFER</h2>
    <ul class="services-list">
      <li><svg class="tick" viewBox="0 0 14 14"><circle cx="6" cy="8" r="5" fill="none" stroke="#f7c21e" stroke-width="1.4"/><path d="M3.5,7.5 L6,10 L12.5,2" fill="none" stroke="#f7c21e" stroke-width="2" stroke-linecap="round"/></svg>Boiler replacements (free quote)</li>
      <li><svg class="tick" viewBox="0 0 14 14"><circle cx="6" cy="8" r="5" fill="none" stroke="#f7c21e" stroke-width="1.4"/><path d="M3.5,7.5 L6,10 L12.5,2" fill="none" stroke="#f7c21e" stroke-width="2" stroke-linecap="round"/></svg>General plumbing &amp; heating</li>
      <li><svg class="tick" viewBox="0 0 14 14"><circle cx="6" cy="8" r="5" fill="none" stroke="#f7c21e" stroke-width="1.4"/><path d="M3.5,7.5 L6,10 L12.5,2" fill="none" stroke="#f7c21e" stroke-width="2" stroke-linecap="round"/></svg>Tap replacements</li>
      <li><svg class="tick" viewBox="0 0 14 14"><circle cx="6" cy="8" r="5" fill="none" stroke="#f7c21e" stroke-width="1.4"/><path d="M3.5,7.5 L6,10 L12.5,2" fill="none" stroke="#f7c21e" stroke-width="2" stroke-linecap="round"/></svg>1st &amp; 2nd</li>
      <li><svg class="tick" viewBox="0 0 14 14"><circle cx="6" cy="8" r="5" fill="none" stroke="#f7c21e" stroke-width="1.4"/><path d="M3.5,7.5 L6,10 L12.5,2" fill="none" stroke="#f7c21e" stroke-width="2" stroke-linecap="round"/></svg>New builds &amp; Extensions</li>
      <li><svg class="tick" viewBox="0 0 14 14"><circle cx="6" cy="8" r="5" fill="none" stroke="#f7c21e" stroke-width="1.4"/><path d="M3.5,7.5 L6,10 L12.5,2" fill="none" stroke="#f7c21e" stroke-width="2" stroke-linecap="round"/></svg>Cylinder replacemets</li>
    </ul>
  </section>

  <section class="booking">
    <h2 class="booking-title">BOOK NOW</h2>
    <p class="contact contact-phone">
      <span class="contact-icon"><svg viewBox="0 0 12 12"><path d="M3,1 L5,3.5 L4,5 Q5,7 7,8 L8.5,7 L11,9 L9.5,11 Q5,11 2.5,7.5 Q1,5 1,2.5 Z" fill="#0c4a96"/></svg></span>07700 914062
    </p>
    <p class="contact contact-phone">
      <span class="contact-icon"><svg viewBox="0 0 12 12"><path d="M1,4 Q6,0 11,4 L10,5.5 L8,5 L8,4 Q6,3 4,4 L4,5 L2,5.5 Z" fill="#0c4a96"/><rect x="2.5" y="6" width="7" height="5" rx="1" fill="#0c4a96"/></svg></span>01632 870215
    </p>
    <p class="contact contact-line">
      <span class="contact-icon"><svg viewBox="0 0 12 12"><rect x="1" y="3" width="10" height="6.5" rx="1" fill="#0c4a96"/><path d="M1.5,3.5 L6,7 L10.5,3.5" fill="none" stroke="#ffffff" stroke-width="0.9"/></svg></span>Info@larkfieldplumbing.example
    </p>
    <p class="contact contact-line">
      <span class="contact-icon"><svg viewBox="0 0 12 12"><circle cx="6" cy="6" r="5" fill="none" stroke="#0c4a96" stroke-width="1.1"/><ellipse cx="6" cy="6" rx="2.2" ry="5" fill="none" stroke="#0c4a96" stroke-width="1"/><line x1="1" y1="6" x2="11" y2="6" stroke="#0c4a96" stroke-width="1"/></svg></span>Larkfield-plumbing.example
    </p>
  </section>
</main>
</body>
</html>
```